Counseling Practice Business Card

I need a professional looking business card incorporating my new logo that was just completed. Card needs to incorporate my name and title, description of my specialty, my address, my phone number, my fax number, my email and my website URL. I need to be able to choose design on/with different paper colors and textures.
I do not have a lot of business card ideas so I am open to anything but I want bold,sharp, clear card without additional designs other than my logo (see attached file info). I am open to different color backgrounds or paper colors including black. I do not like traditional brackets around area codes in phone number or dashes between numbers in phone number. Am open to other ways of presenting including periods between numbers as appropriate. I do not know enough to know what I like yet but I want card to coordinate and work together with my logo. My practice emphasizes natural mental health interventions so any use of color (with background paper color or the blue and green in my logo) that elicits nature is nice. In addition to black, any natural brown or wood looking background might be desirable also. Most of the offerings so far look very similar and boring.

Target Market(s)

Potential therapy clients and other professionals

Contact Information for Business Card

Card information:
Gerald M. Whitcombe, Ph.D.
Licensed Clinical Psychologist
Integrative Health Coach
4812 Marlowe Ridge Blvd SE
Suite 310
Duluth, GA 30096
(770) 415-2983 phone
(770) 581-4096 fax
drgeraldwhitcombe@quillmarsh.net
brightfernwellness.net

Font styles to use
Serif
Sans Serif
Other font styles liked:
• anything that you think looks crisp, clear and easily readable

Requirements
Must have
• Any color used should coordinate with my logo design (see attached files).
• Card should be printed horizontally so top and bottom are longest sides of rectangle.
• Background color or paper color should complement and highlight logo. Do not like a white background. black, grey, brown or any color my logo would blend well with.
Nice to have
• I would like designer to utilize color to highlight letters/name or phone-fax-web symbols.
• Bottom edge of card could be highlighted if appropriate to an idea.
Should not have
• I would NOT want the card to have a pure white background at all.
• No clear cards.
• Cards should be oriented with long sides on bottom and top, NOT sides. DO NOT LIKE THIS THIN TALL ORIENTATION.

```html
<!DOCTYPE html>
<html lang="en">
<head>
<meta charset="utf-8">
<title>Brightfern Wellness – Business Card</title>
<link href="https://fonts.googleapis.com/css2?family=Roboto:wght@400;500;700&display=swap" rel="stylesheet">
<style>
  :root {
    --backdrop: #3a3230;
    --card: #131416;
    --card-edge: #1d1f22;
    --brand-blue: #2d82cc;
    --ink: #f2f2f2;
    --muted: #cfd3d8;
  }
  * { margin: 0; padding: 0; box-sizing: border-box; }
  html, body { width: 1200px; height: 715px; overflow: hidden; }
  body {
    background: var(--backdrop);
    font-family: "Roboto", Arial, sans-serif;
    position: relative;
  }
  .card {
    position: absolute;
    width: 540px;
    height: 309px;
    background: var(--card);
    border-radius: 3px;
    overflow: hidden;
    box-shadow: 0 0 0 1px var(--card-edge);
  }
  .card--front { left: 35px; top: 203px; border-bottom: 5px solid var(--brand-blue); }
  .card--back { left: 625px; top: 203px; }

  .brand {
    position: absolute;
    display: flex;
    align-items: center;
    gap: 10px;
    color: var(--brand-blue);
    font-weight: 700;
    white-space: nowrap;
  }
  .brand__dot {
    width: 14px; height: 14px; border-radius: 50%;
    background: var(--brand-blue);
  }
  .card--front .brand { left: 0; right: 0; top: 112px; justify-content: center; font-size: 36px; }
  .card--front .brand__dot { width: 20px; height: 20px; }
  .front__url {
    position: absolute; left: 0; right: 0; top: 232px;
    text-align: center; color: var(--ink); font-size: 12px; font-weight: 500;
  }

  .card--back .brand { right: 28px; top: 44px; font-size: 22px; }
  .person { position: absolute; left: 30px; top: 28px; }
  .person__name { color: var(--brand-blue); font-size: 18px; font-weight: 700; }
  .person__title { color: var(--ink); font-size: 13px; line-height: 17px; margin-top: 3px; }
  .contact { position: absolute; left: 30px; top: 112px; list-style: none; }
  .contact li {
    display: flex; align-items: center; gap: 8px;
    color: var(--ink); font-size: 13px; line-height: 19px;
  }
  .contact svg { width: 10px; height: 10px; fill: var(--brand-blue); flex: none; }
  .contact .accent { color: var(--brand-blue); }
  .divider {
    position: absolute; left: 30px; right: 28px; top: 100px;
    height: 1.5px; background: var(--ink);
  }
  .address {
    position: absolute; right: 28px; top: 214px; text-align: right;
    color: var(--ink); font-size: 13px; font-weight: 500; line-height: 18px;
  }
  .edge-band { position: absolute; left: 0; bottom: 0; width: 540px; height: 60px; }
</style>
</head>
<body>
  <section class="card card--front">
    <div class="brand"><span class="brand__dot"></span>Brightfern Wellness</div>
    <p class="front__url">www.brightfernwellness.net</p>
  </section>

  <section class="card card--back">
    <div class="person">
      <h1 class="person__name">Gerald M. Whitcombe, Ph.D.</h1>
      <p class="person__title">Licensed Clinical Psychologist<br>Integrative Health Coach</p>
    </div>
    <div class="brand"><span class="brand__dot"></span>Brightfern Wellness</div>
    <div class="divider"></div>
    <ul class="contact">
      <li><svg viewBox="0 0 10 10"><path d="M2 0.5 L4 2.8 L3 4 Q4.5 6 6 7 L7.2 6 L9.5 8 L8 9.6 Q3.5 9 0.4 2 Z"/></svg>(770) 415-2983</li>
      <li><svg viewBox="0 0 10 10"><rect x="2" y="0.5" width="6" height="3"/><rect x="0.5" y="3.5" width="9" height="4" rx="1"/><rect x="2" y="6.5" width="6" height="3"/></svg>(770) 581-4096</li>
      <li><svg viewBox="0 0 10 10"><path d="M0.5 2 H9.5 V8 H0.5 Z M1 2.4 L5 5.6 L9 2.4" fill="none" stroke="#2d82cc" stroke-width="1.1"/></svg>drgeraldwhitcombe@quillmarsh.net</li>
      <li><svg viewBox="0 0 10 10"><circle cx="5" cy="5" r="4.3" fill="none" stroke="#2d82cc" stroke-width="1.1"/><path d="M0.7 5 H9.3 M5 0.7 Q2.5 5 5 9.3 M5 0.7 Q7.5 5 5 9.3" fill="none" stroke="#2d82cc" stroke-width="0.8"/></svg>www.<span class="accent">brightfernwellness</span>.net</li>
    </ul>
    <p class="address">4812 Marlowe Ridge Blvd SE<br>Suite 310 Duluth, GA 30096</p>
    <svg class="edge-band" viewBox="0 0 540 60" preserveAspectRatio="none" aria-hidden="true">
      <path d="M0 18 L300 45 Q320 47 340 50 L540 55 L540 60 L0 60 Z" fill="#2d82cc"/>
      <path d="M0 12 L300 39 Q310 40 318 42" fill="none" stroke="#f2f2f2" stroke-width="2.5"/>
    </svg>
  </section>
</body>
</html>
```